Business Card for a Creative Technology based HR services company

Our company name is Lumo8, and we build large communities of HR (human resource) and finance personnels through our mobile platform, and we conduct lots of on-line and off-line activities to get everyone constantly connected. Behind all these, we will also provide on-site HR and finance contractors to our clients, plus a host of other HR-related services. No process in our company takes more than 5-steps.
Our company slogan: Touching Your Future
Target Market(s)
All human resource (HR) and finance personnels, from new entrants to highly experienced senior professionals.
Industry/Entity Type
Finance
Colors
Designer to choose colors to be used in the design.
Look and feel
Each slider illustrates characteristics of the customer's brand and the style your logo design should communicate.

```html
<!DOCTYPE html>
<html lang="en">
<head>
<meta charset="utf-8">
<title>Lumo8 Business Card</title>
<link rel="stylesheet" href="https://fonts.googleapis.com/css2?family=Michroma&family=Montserrat:wght@400;500&display=swap">
<style>
  :root {
    --backdrop: #e9e6e1;
    --card-white: #ffffff;
    --navy: #0f2a50;
    --ink: #2b2b2b;
    --muted: #555a60;
  }
  * { margin: 0; padding: 0; box-sizing: border-box; }
  html, body { width: 1200px; height: 672px; overflow: hidden; }
  body {
    background: var(--backdrop);
    display: flex;
    align-items: center;
    justify-content: center;
    gap: 72px;
    font-family: "Montserrat", sans-serif;
  }
  .card {
    width: 336px;
    height: 560px;
    border-radius: 4px;
    box-shadow: 0 10px 30px rgba(0,0,0,0.18);
    position: relative;
    overflow: hidden;
  }
  .card-front { background: var(--card-white); }
  .card-back { background: var(--navy); }

  .brand {
    position: absolute;
    top: 100px;
    left: 0;
    right: 0;
    text-align: center;
  }
  .brand-name {
    font-family: "Michroma", sans-serif;
    font-weight: 400;
    font-size: 34px;
    color: var(--ink);
    letter-spacing: 2px;
  }

  .person {
    position: absolute;
    top: 300px;
    left: 34px;
    right: 20px;
  }
  .person-name {
    font-family: "Michroma", sans-serif;
    font-size: 18px;
    color: var(--ink);
    letter-spacing: 0.5px;
    white-space: nowrap;
  }
  .person-title {
    font-family: "Michroma", sans-serif;
    font-size: 8px;
    color: var(--muted);
    letter-spacing: 1px;
    margin-top: 4px;
  }

  .contact-list {
    position: absolute;
    top: 360px;
    left: 34px;
    right: 20px;
    list-style: none;
    display: flex;
    flex-direction: column;
    gap: 9px;
  }
  .contact-item {
    display: flex;
    align-items: flex-start;
    gap: 10px;
    font-size: 11px;
    color: var(--ink);
    line-height: 1.45;
  }
  .contact-icon {
    width: 18px;
    height: 18px;
    flex: 0 0 18px;
    background: var(--ink);
    border-radius: 2px;
    display: flex;
    align-items: center;
    justify-content: center;
  }
  .contact-icon svg { width: 12px; height: 12px; }
  .contact-text { padding-top: 1px; }
</style>
</head>
<body>
  <section class="card card-front" aria-label="Business card front">
    <div class="brand">
      <span class="brand-name">Lumo8</span>
    </div>

    <div class="person">
      <p class="person-name">DANIEL REYES</p>
      <p class="person-title">GENERAL MANAGER</p>
    </div>

    <ul class="contact-list">
      <li class="contact-item">
        <span class="contact-icon">
          <svg viewBox="0 0 12 12"><path d="M3 1.5 L4.8 3.6 L3.9 4.8 Q5 7 7.2 8.1 L8.4 7.2 L10.5 9 L9.4 10.5 Q4.5 10 1.5 2.6 Z" fill="#fff"/></svg>
        </span>
        <span class="contact-text">021 480 3357<br>021 480 3358</span>
      </li>
      <li class="contact-item">
        <span class="contact-icon">
          <svg viewBox="0 0 12 12"><rect x="1.5" y="3" width="9" height="6.5" fill="none" stroke="#fff" stroke-width="1.2"/><path d="M1.5 3 L6 7 L10.5 3" fill="none" stroke="#fff" stroke-width="1.2"/></svg>
        </span>
        <span class="contact-text">daniel@lumo8mail.com</span>
      </li>
      <li class="contact-item">
        <span class="contact-icon">
          <svg viewBox="0 0 12 12"><circle cx="6" cy="6" r="4.5" fill="none" stroke="#fff" stroke-width="1.1"/><ellipse cx="6" cy="6" rx="2" ry="4.5" fill="none" stroke="#fff" stroke-width="1"/><path d="M1.5 6 H10.5" stroke="#fff" stroke-width="1"/></svg>
        </span>
        <span class="contact-text">www.lumo8hr.com</span>
      </li>
      <li class="contact-item">
        <span class="contact-icon">
          <svg viewBox="0 0 12 12"><path d="M6 11 Q2 6.5 2 4.5 A4 4 0 0 1 10 4.5 Q10 6.5 6 11 Z" fill="#fff"/><circle cx="6" cy="4.5" r="1.4" fill="#2b2b2b"/></svg>
        </span>
        <span class="contact-text">27, 9th Floor, Harbour Point<br>Road NWD</span>
      </li>
    </ul>
  </section>

  <section class="card card-back" aria-label="Business card back"></section>
</body>
</html>
```